Probate (Legal) Wordpress Design with Coding for Online Company

I need a Wordpress design with coding, pictures, content to be provided by me, fully responsive, and development. This is for a 6-7 page design.

Pages Needed: Home/About/Probate/Process/FAQ/Contact Us/Blog.

The home page should be organized as followed:
-Steps in Probate: Gather; Implement; Close (each step will come with content)
-Flat-Fee Price & Savings: Content will go here with a button to contact us (phone number) or just the phone number.
-You Have Questions, We Have Answers: five questions with content. Only one question answer to show at a time when clicked on the question from the list.
-Get to Know Us: a brief description with content about what we do and who we are.

Main image slogan: Helping Californians deal with loss with DIGNITY & UNDERSTATING (you may use a better slogan if you wish).

The Contact page should not have a map since we are an online company. We service the entire state of California in every county and city.

The About page should be simple, direct, and easy on the eye. It should have a brief description of who we are and it should have no more than 6 reasons why the client should hire us.

About our online California company. We are not attorneys but legal document assistants who prepare legal documents for probate estate when someone dies with or without a will and assets need to be distributed. We have a flat-fee for Formal Probate of $999 and $699 for Informal Probate. We are an online company and offer our services to the entire state of California in every county. We do everything over the phone and email. The turn around time for us to prepare the initial legal paperwork for the client is within 3-5 business days. We can prepare, file, serve and manage a probate matter from petition to closing. We are not attorneys so our prices are very affordable compare to the attorney.

The company name for the website will be www.velmarhollow.com, The Velmar Hollow Group.

I do not have a logo yet. The colors of the website should be easy on the eye and calming. THE SITE SHOULD BE SIMPLE AND STRAIGHT TO THE POINT. EASY TO NAVIGATE.

The company phone number should be very visible and should stand out to the client. It should also be clickable and ready to dial for smartphone users.

I do not want a contact form on the homepage. THE MAIN THING IS FOR THE POTENTIAL CLIENT TO CALL OUR OFFICE TO SIGN UP.

I do like some images of family or people since we are dealing with people who just lost a loved one. Not all the images have to be of people.

The site should not look like we practice law or that people can mistake us for attorneys.

Target Market(s)

People who just lost a loved one who had property, assets, in California but died with or without a will or trust. This is for people looking to hire non-attorneys.

Coding

Coded - Design and coding required

Font styles to use
Serif

Colors

Designer to choose colors to be used in the design.

Requirements
Must have
• Refer to Project Description.
Nice to have
• The sample images provided is what I am attracted to for the homepage image.
Should not have

```html
<!DOCTYPE html>
<html lang="en">
<head>
<meta charset="utf-8">
<title>The Velmar Hollow Group</title>
<link href="https://fonts.googleapis.com/css2?family=Open+Sans:wght@400;600;700&family=Roboto+Condensed:wght@400;700&display=swap" rel="stylesheet">
<style>
:root{
  --ink:#1d1d1d;
  --text:#555;
  --muted:#777;
  --blue:#1d74c2;
  --line:#d8d8d8;
  --soft:#f1f1f1;
  --white:#fff;
  --footer:#0d0d0d;
}
*{box-sizing:border-box;margin:0;padding:0}
html,body{width:1200px;height:3789px;overflow:hidden}
body{font-family:"Open Sans",Arial,sans-serif;color:var(--text);background:var(--white);position:relative}
h1,h2,h3{font-family:"Roboto Condensed","Arial Narrow",sans-serif;font-weight:400;color:var(--ink)}

/* header */
.site-header{position:absolute;left:0;top:0;width:1200px;height:157px;background:var(--white)}
.brand{position:absolute;left:88px;top:58px;font-family:"Roboto Condensed",sans-serif;font-weight:700;font-size:26px;line-height:32px;color:var(--ink);white-space:nowrap}
.top-contact{position:absolute;top:38px;left:585px;display:flex;align-items:center;gap:14px;font-size:16px;color:var(--text)}
.top-contact .ic{width:36px;height:36px;border:2px solid #bbb;border-radius:50%;display:flex;align-items:center;justify-content:center}
.top-contact .item{display:flex;align-items:center;gap:10px;margin-right:14px}
.socials{display:flex;gap:6px}
.socials span{width:20px;height:20px;border-radius:3px;display:block}
.main-nav{position:absolute;top:93px;left:0;width:1200px;height:24px;font-size:16px;color:var(--ink)}
.main-nav a{position:absolute;text-decoration:none;color:var(--ink)}
.main-nav a.active{color:var(--blue)}

/* hero */
.hero{position:absolute;left:0;top:157px;width:1200px;height:525px;background:linear-gradient(100deg,#3e5a26 0%,#5b7a34 35%,#7f9a4a 60%,#a9b86a 80%,#c7cf93 100%)}
.hero-text{position:absolute;left:560px;top:208px;width:548px;text-align:right;font-family:"Roboto Condensed",sans-serif;font-size:33px;line-height:46px;color:var(--white)}
.slide-arrow{position:absolute;top:392px;width:14px;height:14px;color:var(--white);font-size:14px}

/* steps */
.section-title{position:absolute;left:0;width:1200px;text-align:center;font-size:31px;font-family:"Roboto Condensed",sans-serif;color:var(--ink)}
.step{position:absolute;top:855px;width:300px;text-align:center}
.step .circle{width:108px;height:108px;border:2px solid #999;border-radius:50%;margin:0 auto;display:flex;align-items:center;justify-content:center}
.step h3{font-family:"Open Sans",sans-serif;font-size:20px;margin-top:24px;color:var(--ink)}
.step p{font-size:14px;line-height:20px;margin-top:12px;color:var(--text)}
.step .more{font-size:12px;color:var(--blue);margin-top:8px;display:block}

/* about */
.about-band{position:absolute;left:0;top:1170px;width:1200px;height:518px;background:linear-gradient(135deg,#f4f4f4,#e6e6e6 50%,#f2f2f2)}
.about-card{position:absolute;left:136px;top:1273px;width:907px;height:328px;background:var(--white);box-shadow:0 4px 14px rgba(0,0,0,.18)}
.about-card h2{position:absolute;left:46px;top:50px;font-family:"Open Sans",sans-serif;font-size:29px;font-weight:400;color:var(--ink)}
.about-card p{position:absolute;left:46px;top:100px;width:428px;font-size:13.5px;line-height:21px;text-align:justify;color:var(--text)}
.btn{display:inline-block;background:var(--blue);color:var(--white);border-radius:18px;font-size:11px;text-transform:uppercase;padding:9px 18px}
.about-card .btn{position:absolute;left:46px;top:246px}
.about-photo{position:absolute;left:518px;top:0;width:389px;height:328px;background:linear-gradient(135deg,#d6e4ee,#8aa4b8 50%,#3f5160)}

/* pricing */
.pricing{position:absolute;left:0;top:1688px;width:1200px;height:442px;background:linear-gradient(90deg,#2a1c2a 0%,#5a3a3a 25%,#3c2c3e 45%,#1c1d2e 70%,#111426 100%)}
.pricing-copy{position:absolute;left:561px;top:1786px;width:560px;color:var(--white)}
.pricing-copy h2{color:var(--white);font-size:31px;font-family:"Roboto Condensed",sans-serif}
.pricing-copy ul{list-style:none;margin-top:18px;font-size:13px;line-height:24px}
.pricing-copy li{display:flex;align-items:center;gap:8px}
.pricing-copy p{font-size:13px;line-height:24px;margin-top:6px}
.pricing-copy .btn{margin-top:18px;text-transform:none;font-size:12px;padding:7px 16px}

/* faq */
.faq{position:absolute;left:172px;width:859px;background:var(--white);border-left:6px solid var(--blue);box-shadow:0 2px 6px rgba(0,0,0,.2);padding:0 20px 0 26px;font-size:15px;color:var(--ink)}
.faq .q{height:61px;display:flex;align-items:center;justify-content:space-between}
.faq .a{font-size:13px;color:var(--text);padding-bottom:20px;border-top:1px solid #eee;padding-top:10px}
.faq .tog{width:20px;height:20px;border:2px solid var(--blue);color:var(--blue);border-radius:3px;font-size:16px;line-height:14px;text-align:center;flex:none}

/* know us */
.know{position:absolute;left:0;top:2804px;width:1200px;height:462px;background:var(--soft)}
.know-card{position:absolute;top:2973px;width:500px;height:185px;background:var(--white);box-shadow:0 2px 6px rgba(0,0,0,.12)}
.know-card .photo{position:absolute;left:0;top:0;width:162px;height:185px}
.know-card h3{position:absolute;left:187px;top:28px;font-family:"Open Sans",sans-serif;font-size:20px;color:var(--ink)}
.know-card p{position:absolute;left:187px;top:68px;width:292px;font-size:13px;line-height:21px;text-align:justify;color:var(--text)}
.know-card .more{position:absolute;left:187px;top:140px;font-size:13px;color:var(--blue)}

/* partners */
.badge{position:absolute;top:3329px;height:99px;background:#f5f5f5;border:1px solid #e6e6e6;box-shadow:0 1px 3px rgba(0,0,0,.1)}
.badge span{position:absolute;left:50%;top:50%;width:70px;height:16px;margin:-8px 0 0 -35px;background:#c9c9c9;border-radius:3px}

/* footer */
.site-footer{position:absolute;left:0;top:3486px;width:1200px;height:303px;background:var(--footer);color:#ddd}
.site-footer .brand{left:110px;top:120px;font-size:24px;color:var(--white)}
.fcol{position:absolute;top:62px;font-size:12px;line-height:24px}
.fcol h4{font-size:14px;color:var(--white);font-weight:600;margin-bottom:10px;text-transform:uppercase}
.fcol li{list-style:none}
.fsocial{display:flex;gap:10px;margin-top:4px}
.fsocial span{width:28px;height:28px;border-radius:50%;background:var(--white)}
.copyright{position:absolute;left:0;top:3742px;width:1200px;text-align:center;font-size:12px;color:#bbb;border-top:1px solid #333;padding-top:10px}
</style>
</head>
<body>

<header class="site-header">
  <div class="brand">The Velmar Hollow Group</div>
  <div class="top-contact">
    <div class="item"><span class="ic"><svg width="16" height="16" viewBox="0 0 24 24"><path fill="#777" d="M6.6 10.8a15 15 0 0 0 6.6 6.6l2.2-2.2c.3-.3.7-.4 1-.2 1.1.4 2.3.6 3.6.6.6 0 1 .4 1 1V20c0 .6-.4 1-1 1A17 17 0 0 1 3 4c0-.6.4-1 1-1h3.5c.6 0 1 .4 1 1 0 1.3.2 2.5.6 3.6.1.3 0 .7-.2 1z"/></svg></span>555.014.2290</div>
    <div class="item"><span class="ic"><svg width="16" height="16" viewBox="0 0 24 24"><rect x="3" y="5" width="18" height="14" fill="#777"/><path d="M3 5l9 7 9-7" stroke="#fff" stroke-width="1.5" fill="none"/></svg></span>info@velmarhollow.com</div>
    <div class="socials"><span style="background:#3b5b98"></span><span style="background:#2aa3ef"></span><span style="background:#0a77b5"></span><span style="background:#d8433b"></span></div>
  </div>
  <nav class="main-nav">
    <a class="active" style="left:424px">Home</a>
    <a style="left:523px">About</a>
    <a style="left:624px">Probate</a>
    <a style="left:735px">Process</a>
    <a style="left:851px">FAQ</a>
    <a style="left:935px">Contact Us</a>
    <a style="left:1074px">Blog</a>
  </nav>
</header>

<section class="hero" role="img" aria-label="A smiling family of three walking together along a leafy woodland path">
  <h1 class="hero-text">Helping Californians deal with loss<br>with DIGNITY &amp; UNDERSTATING</h1>
  <span class="slide-arrow" style="left:100px">&#8249;</span>
  <span class="slide-arrow" style="left:141px">&#8250;</span>
  <span class="slide-arrow" style="left:1065px">&#8249;</span>
  <span class="slide-arrow" style="left:1094px">&#8250;</span>
</section>

<h2 class="section-title" style="top:763px">STEPS IN PROBATE</h2>
<div class="step" style="left:133px">
  <div class="circle"><svg width="40" height="40" viewBox="0 0 24 24"><path fill="#1d74c2" d="M2 10h4v11H2zM8 21h10c.8 0 1.5-.5 1.8-1.2l2.2-6V12c0-1.1-.9-2-2-2h-6l1-4.6c.1-.6-.1-1.1-.5-1.5L13.4 3 8 8.4z"/></svg></div>
  <h3>Gather</h3>
  <p>It is a long established fact that a<br>reader will be distracted by the read-</p>
  <span class="more">Learn More &rarr;</span>
</div>
<div class="step" style="left:451px">
  <div class="circle"><svg width="40" height="40" viewBox="0 0 24 24"><path fill="#1d74c2" d="M4 8h4a2.5 2.5 0 1 1 5 0h4v4a2.5 2.5 0 1 1 0 5v4h-4a2.5 2.5 0 1 0-5 0H4v-4a2.5 2.5 0 1 0 0-5z"/></svg></div>
  <h3>Implement</h3>
  <p>It is a long established fact that a<br>reader will be distracted by the read-</p>
  <span class="more">Learn More &rarr;</span>
</div>
<div class="step" style="left:769px">
  <div class="circle"><svg width="44" height="40" viewBox="0 0 26 24"><g fill="#1d74c2"><circle cx="13" cy="7" r="3.5"/><circle cx="5" cy="9" r="2.6"/><circle cx="21" cy="9" r="2.6"/><path d="M7 19c0-3.5 2.7-6 6-6s6 2.5 6 6zM0 19c0-3 2-4.5 5-4.5 1 0 1.6.2 2 .4-.9 1.2-1.3 2.6-1.3 4.1zM26 19c0-3-2-4.5-5-4.5-1 0-1.6.2-2 .4.9 1.2 1.3 2.6 1.3 4.1z"/></g></svg></div>
  <h3>Lenders</h3>
  <p>It is a long established fact that a<br>reader will be distracted by the read-</p>
  <span class="more">Learn More &rarr;</span>
</div>

<section class="about-band"></section>
<article class="about-card">
  <h2>ABOUT US</h2>
  <p>About our online California company. We are not attorneys but legal document assistants who prepare legal documents for probate estate when someone dies with or without a will and assets need to be distributed. We have a flat-fee for Formal Probate of $999 and $699 for Informal Probate. We are an online company and offer our services to the entire state of California</p>
  <span class="btn">Read more</span>
  <div class="about-photo" role="img" aria-label="Hands working on a laptop and paperwork at an office desk"></div>
</article>

<section class="pricing" role="img" aria-label="A lit suspension bridge and city skyline at dusk"></section>
<div class="pricing-copy">
  <h2>Flat-Fee Price &amp; Savings</h2>
  <ul>
    <li><svg width="12" height="12" viewBox="0 0 12 12"><rect x=".5" y=".5" width="11" height="11" fill="none" stroke="#fff"/><path d="M2.5 6l2.5 2.5 4.5-5" stroke="#fff" fill="none" stroke-width="1.5"/></svg>Condimentum eros pretium nam vel magnas nec diam.</li>
    <li><svg width="12" height="12" viewBox="0 0 12 12"><rect x=".5" y=".5" width="11" height="11" fill="none" stroke="#fff"/><path d="M2.5 6l2.5 2.5 4.5-5" stroke="#fff" fill="none" stroke-width="1.5"/></svg>Diam commodo viverra eget leo curabitur diam consequat</li>
    <li><svg width="12" height="12" viewBox="0 0 12 12"><rect x=".5" y=".5" width="11" height="11" fill="none" stroke="#fff"/><path d="M2.5 6l2.5 2.5 4.5-5" stroke="#fff" fill="none" stroke-width="1.5"/></svg>Nam luctus venenatis mauris et luctus sem lacinia et.</li>
  </ul>
  <p>We are not attorneys but legal document assistants who prepare legal documents for pro-<br>bate estate when someone dies with or without a will and assets need to be distributed.</p>
  <span class="btn">Contact us &raquo;</span>
</div>

<h2 class="section-title" style="top:2210px">FAQ</h2>
<div class="faq" style="top:2288px">
  <div class="q" style="height:52px">Q- Neque porro quisquam est qui dolorem ipsum quia dolor sit amet, consectetur ?<span class="tog">&minus;</span></div>
  <div class="a">A-Lorem Ipsum is simply dummy text of the printing and typesetting industryLorem Ipsum is simply dummy text</div>
</div>
<div class="faq" style="top:2392px"><div class="q">Q- What porro quisquam est qui dolorem ipsum quia dolor porro quisquam est qui ?<span class="tog">+</span></div></div>
<div class="faq" style="top:2466px"><div class="q">Q- What is the quisquam est qui dolorem ipsum quia dolor sit amet, consectetur ?<span class="tog">+</span></div></div>
<div class="faq" style="top:2540px"><div class="q">Q- What is the quisquam est qui dolorem ipsum quia dolor sit amet, adipisci velit?<span class="tog">+</span></div></div>
<div class="faq" style="top:2614px"><div class="q">Q- What is dolorem ipsum quia dolor sit amet, consectetur, adipisci velit quisquam est qui ?<span class="tog">+</span></div></div>

<section class="know"></section>
<h2 class="section-title" style="top:2877px">Get to Know Us</h2>
<div class="know-card" style="left:93px">
  <div class="photo" role="img" aria-label="Business person typing on a laptop" style="background:linear-gradient(135deg,#c9d6e0,#55687a)"></div>
  <h3>What We Do</h3>
  <p>Lorem Ipsum has been the industry's standard dummy text ever since the 1500s, when an unknown printer took a galley</p>
  <span class="more">Read More &gt;&gt;</span>
</div>
<div class="know-card" style="left:611px">
  <div class="photo" role="img" aria-label="Colleagues reviewing charts and documents at a table" style="background:linear-gradient(135deg,#dfe5ea,#7c8c9a)"></div>
  <h3>Who We Are</h3>
  <p>Lorem Ipsum has been the industry's standard dummy text ever since the 1500s, when an unknown printer took a galley</p>
  <span class="more">Read More &gt;&gt;</span>
</div>

<div class="badge" style="left:149px;width:169px"><span></span></div>
<div class="badge" style="left:331px;width:172px"><span></span></div>
<div class="badge" style="left:515px;width:170px"><span></span></div>
<div class="badge" style="left:697px;width:172px"><span></span></div>
<div class="badge" style="left:882px;width:169px"><span></span></div>

<footer class="site-footer">
  <div class="brand">The Velmar Hollow Group</div>
  <div class="fcol" style="left:392px">
    <h4>Information</h4>
    <ul><li>&raquo; Privacy Policy</li><li>&raquo; Login</li><li>&raquo; Advanced Search</li><li>&raquo; Contact Us</li></ul>
  </div>
  <div class="fcol" style="left:644px">
    <h4>Contact Us</h4>
    <ul><li>Address : 12 Cedar Lane, Fairhaven,</li><li>California</li><li>Phone : (555) 014-7731</li><li>Email : info@velmarhollow.com</li></ul>
  </div>
  <div class="fcol" style="left:935px">
    <h4>Follow us out there</h4>
    <div class="fsocial"><span></span><span></span><span></span></div>
  </div>
</footer>
<div class="copyright">Copyright &copy; 2017 All Rights Reserved</div>

</body>
</html>
```